Design a Google site for a travel agency

I own a travel agency and I would like to have a Google site built for my company called Harborquestjourneys.com by Bright Path Holidays. Our specialty Cruising and adventure. We create a lot of custom tour of Europe and Peru. Our Adventure tours targets mainly women from 25 to 65. I would like to site especially the cruise to appeal to family but also upscale more expensive upscale clientele.
Updates

I would like to shift away from create a new site with multiple pages to one simple Google Site page with a Contact us page and testimonials. The sites theme is Cruise & Adventure Travel. We specialize in selling cruises and building custom travel tours around the world.

Target Market(s)

Cruisers and adventure travelers for women from 25 to 70

Industry/Entity Type

travel industry with a focus on cruising and adventure travel

Coding

Coded - Design and coding required

Number of Pages Required

5+ page

Font styles to use
Serif
Sans Serif

Requirements
Must have
• Home page, Cruise, Adventure Tours, Testimonials, About Us
Nice to have
• Auto place https://www.brightpathholidays.ca/offers into the site.
Should not have
• beach resorts

```html
<!DOCTYPE html>
<html lang="en">
<head>
<meta charset="utf-8">
<title>Bright Path Holidays — Adventure Travel &amp; Ocean Cruises</title>
<link rel="stylesheet" href="https://fonts.googleapis.com/css2?family=Cinzel:wght@400;500;600&family=Roboto:wght@400;500;700&display=swap">
<style>
:root{
  --stage:#9a9696;
  --sky:#29a7df;
  --link:#1f9fdb;
  --navy:#0b4a66;
  --amber:#f5a623;
  --ink:#1d1d1d;
  --muted:#5a5a5a;
  --line:#cfd6da;
  --white:#ffffff;
}
*{box-sizing:border-box;margin:0;padding:0}
html,body{width:1200px;height:1124px;overflow:hidden}
body{background:var(--stage);font-family:'Roboto',sans-serif;position:relative}
.page{position:absolute;top:95px;width:516px;height:935px;background:var(--white);overflow:hidden}
.page--adventure{left:71px}
.page--cruise{left:613px}
.hero{position:absolute;left:0;top:0;width:516px;height:159px;background:var(--sky)}
.brand{position:absolute;left:62px;top:16px;display:flex;flex-direction:column;align-items:center;gap:4px;color:var(--white);font-family:'Roboto',sans-serif;font-weight:400;font-size:10px;letter-spacing:.3px}
.brand__mark{width:16px;height:16px;border-radius:50%;background:var(--white)}
.nav{position:absolute;left:199px;top:25px;width:256px;display:flex;justify-content:space-between;font-size:5.6px;font-weight:700;color:var(--white)}
.nav span:first-child{font-weight:400;opacity:.85}
.hero__title{position:absolute;left:60px;top:84px;font-family:'Cinzel',serif;font-weight:500;font-size:23px;line-height:25px;color:var(--white)}
.hero__photo{position:absolute;left:243px;top:52px;width:211px;height:108px;border:2px solid var(--amber);border-bottom:none}
.intro{position:absolute;left:68px;top:177px;width:381px;font-size:5.8px;line-height:11.4px;color:var(--muted);text-align:justify}
.intro p+p{margin-top:11.4px}
.section-title{position:absolute;left:0;width:516px;text-align:center;font-family:'Cinzel',serif;color:var(--ink)}
.section-title--partners{top:295px;font-size:13px}
.section-title--offers{top:418px;font-size:17px}
.partners{position:absolute;left:65px;top:330px;display:flex;gap:7px}
.partner{width:92px;height:39px;border:1px solid var(--line);display:flex;align-items:center;justify-content:center;gap:4px;font-size:6.6px;font-weight:500;color:#2a2a2a;text-transform:uppercase;text-align:center;line-height:7px}
.partner__dot{width:9px;height:9px;border-radius:50%;background:#2a2a2a;flex:none}
.arrow{position:absolute;top:343px;width:10px;height:10px}
.arrow--prev{left:44px}
.arrow--next{left:463px}
.offers{position:absolute;left:62px;width:394px;display:grid;grid-template-columns:repeat(3,127px);column-gap:6px}
.offers--row1{top:457px}
.offer__photo{width:127px;height:95px}
.offer__title{margin-top:8px;font-size:7.6px;line-height:10.6px;font-weight:500;color:var(--link);text-transform:uppercase}
.offer__text{margin-top:5px;font-size:5.4px;line-height:8.2px;color:var(--muted)}
.footer{position:absolute;left:0;top:822px;width:516px;height:113px;background:var(--navy);color:var(--white);font-size:6.8px}
.footer__col{position:absolute;top:20px;display:flex;flex-direction:column;gap:9px}
.footer__col--left{left:63px}
.footer__col--right{left:258px}
.footer__row{display:flex;align-items:center;gap:9px}
.footer__row svg{width:8px;height:8px;flex:none}
.social{position:absolute;left:419px;top:22px;display:flex;gap:12px}
.social span{width:11px;height:11px;border-radius:50%;background:var(--white)}
.copyright{position:absolute;left:0;top:76px;width:516px;text-align:center}
</style>
</head>
<body>

<!-- Adventure Travel page -->
<section class="page page--adventure">
  <header class="hero">
    <div class="brand"><span class="brand__mark"></span>BrightPathHolidays</div>
    <nav class="nav"><span>About Us</span><span>Experiences</span><span>Tours</span><span>Offers</span><span>Blogs</span><span>Contest</span><span>Testimonials</span><span>More</span></nav>
    <h1 class="hero__title">Adventure<br>Travel</h1>
    <div class="hero__photo" role="img" aria-label="Hiker with a yellow backpack in a green mountain meadow" style="background:linear-gradient(180deg,#b9c8c2 0%,#6f8a5a 30%,#5e7b3a 65%,#7b8d3c 100%)"></div>
  </header>

  <div class="intro">
    <p>If you are seeking a journey like no other, then this one is for you.<br>The days of adventure travel consisting of a dusty tent with nothing but a cot to sleep on are long gone; welcome to the new adventure travel option. From safaris in Africa, to a walkabout in the Australian outback, to hiking the Inca trails of Peru, adventure travel is limitless.</p>
    <p>You can choose a relaxed approach to light physical activity or go for the full physical experience and make being active a huge part of your experience; the possibilities are limitless. Adventure travel provides you as much or as little physical exertion as you want, the choice is entirely up to you.Adventure travel provides you with the chance to experience the people and the culture in a new and fascinating way that is sure to thrill your senses and leave you with stories to tell for years.</p>
  </div>

  <h2 class="section-title section-title--partners">Our Top Adventure Vacation Partners</h2>
  <svg class="arrow arrow--prev" viewBox="0 0 10 10"><path d="M9 5H1M4 2L1 5l3 3" fill="none" stroke="#333" stroke-width=".8"/></svg>
  <div class="partners">
    <div class="partner"><span class="partner__dot"></span>Northwake<br>Expeditions</div>
    <div class="partner">Trailbound<br>North</div>
    <div class="partner">DMX Global</div>
    <div class="partner">Seaward Voyages</div>
  </div>
  <svg class="arrow arrow--next" viewBox="0 0 10 10"><path d="M1 5h8M6 2l3 3-3 3" fill="none" stroke="#333" stroke-width=".8"/></svg>

  <h2 class="section-title section-title--offers">Best Offers for Adventure</h2>
  <div class="offers offers--row1">
    <article>
      <div class="offer__photo" role="img" aria-label="Child riding a colourful carousel horse" style="background:linear-gradient(160deg,#3b8fc4,#d9a24a 55%,#b8443a)"></div>
      <h3 class="offer__title">Starting from $879CAD per person - Nashville</h3>
      <p class="offer__text">5-Nights | Music, Moonshine &amp; More | Nashville, Tennessee | Packages Available from June 8 - December 31, 2022</p>
    </article>
    <article>
      <div class="offer__photo" role="img" aria-label="City skyline and bridge at dusk over a river" style="background:linear-gradient(180deg,#6f6fb0,#c88aa8 45%,#4a3f7a 70%,#2c2a55)"></div>
      <h3 class="offer__title">Take on a bolder tropic trek!</h3>
      <p class="offer__text">Allure Horizon May 14, 2023 Departure | 7-Night Western Caribbean Cruise | Offer Expires October 2, 2022</p>
    </article>
    <article>
      <div class="offer__photo" role="img" aria-label="Colourful riverside houses along a canal" style="background:linear-gradient(180deg,#d8e4ec,#b86a4a 40%,#3f8fae 80%)"></div>
      <h3 class="offer__title">Save $150CAD per couple - Highlights of Malaysia</h3>
      <p class="offer__text">Save $150CAD Per Person if booked up to 3-months in advance | 10-Day First Class Accommodations | Visiting Kuala Lumpur,</p>
    </article>
  </div>
  <div class="offers" style="top:629px">
    <article>
      <div class="offer__photo" role="img" aria-label="Green karst mountains with wildflowers" style="background:linear-gradient(180deg,#8fc3e8,#3f7a5a 45%,#5b9a2e)"></div>
      <h3 class="offer__title">Book early and save - Vietnam at a glance</h3>
      <p class="offer__text">Save $150CAD Per Couple When you Book 3 months in advance | Vietnam | Offer Expires September 10, 2022</p>
    </article>
    <article>
      <div class="offer__photo" role="img" aria-label="Ship observation capsule above a glacier bay" style="background:linear-gradient(180deg,#5a9fd6,#cfe2ee 50%,#6a8fa6)"></div>
      <h3 class="offer__title">Discover the best of Alaska from one charming town to the next</h3>
      <p class="offer__text">Ovation Star May 11, 2023 Departure | 8 Night Alaska Glacier Cruise | Offer Expires October 2, 2022</p>
    </article>
    <article>
      <div class="offer__photo" role="img" aria-label="Floating market boat loaded with fresh fruit" style="background:linear-gradient(160deg,#6b5a3a,#c9b24a 45%,#2f5e86)"></div>
      <h3 class="offer__title">Book early - save $120CAD per couple on amazing Thailand</h3>
      <p class="offer__text">Save $120CAD Per Couple | Bangkok, Phitsanuloke, Chiang &amp; Chiang Mai | Offer Expires September 22, 2022</p>
    </article>
  </div>

  <footer class="footer">
    <div class="footer__col footer__col--left">
      <div class="footer__row"><svg viewBox="0 0 8 8"><circle cx="4" cy="4" r="3.5" fill="#f5a623"/><path d="M4 2v2h1.5" stroke="#0b4a66" stroke-width=".8" fill="none"/></svg>Hours 07:45 - 16:00 (AT)</div>
      <div class="footer__row"><svg viewBox="0 0 8 8"><path d="M4 .5a2.6 2.6 0 0 1 2.6 2.6C6.6 5 4 7.5 4 7.5S1.4 5 1.4 3.1A2.6 2.6 0 0 1 4 .5z" fill="#f5a623"/></svg>12 Harbour Lane, Douglas, NB, E3G 1A1, Canada</div>
    </div>
    <div class="footer__col footer__col--right">
      <div class="footer__row"><svg viewBox="0 0 8 8"><path d="M1.5 1l1.5-.5 1 2-1 .8a4 4 0 0 0 1.7 1.7l.8-1 2 1-.5 1.5C3.5 7 1 4.5 1.5 1z" fill="#f5a623"/></svg>555-014-2290</div>
      <div class="footer__row"><svg viewBox="0 0 8 8"><rect x=".5" y="1.5" width="7" height="5" fill="#f5a623"/><path d="M.5 1.5L4 4.3l3.5-2.8" stroke="#0b4a66" stroke-width=".6" fill="none"/></svg>hello@brightpathholidays.ca</div>
    </div>
    <div class="social"><span></span><span></span></div>
    <p class="copyright">© 2022 Bright Path Holidays &nbsp;|&nbsp; Privacy Policy &nbsp;|&nbsp; Terms of Use</p>
  </footer>
</section>

<!-- Ocean Cruises page -->
<section class="page page--cruise">
  <header class="hero">
    <div class="brand"><span class="brand__mark"></span>BrightPathHolidays</div>
    <nav class="nav"><span>About Us</span><span>Experiences</span><span>Tours</span><span>Offers</span><span>Blogs</span><span>Contest</span><span>Testimonials</span><span>More</span></nav>
    <h1 class="hero__title">Ocean<br>Cruises</h1>
    <div class="hero__photo" role="img" aria-label="Large white cruise ship sailing on deep blue sea" style="background:linear-gradient(180deg,#3d6ea3,#1f4f86 50%,#173f70)"></div>
  </header>

  <div class="intro">
    <p>Fasting growing travel experience for Canadians.<br>Until you have watched the sunset on the ocean horizon and seen the star's twinkle reflected off the great waters, you don't know what you are missing. Cruising is a style of travel that you are sure to fall in love with. Choose one of the premium brands and take a 5-star cruise around Asia, Australia or even South America. Take the family on-board a cruise that has something magical for every member no matter the age. Explore the shores of Europe in a truly original way with a river cruise where the views outside your window are history coming to life. Cruising is more than just laying by the pool and eating in a cafeteria style eatery. Fine dining, heaps of on-board activities, entertainment that gives Broadway a run for its money and more. What are you waiting for? Plan your cruise today!</p>
  </div>

  <h2 class="section-title section-title--partners">Our Top Ocean Cruises Vacation Partners</h2>
  <svg class="arrow arrow--prev" viewBox="0 0 10 10"><path d="M9 5H1M4 2L1 5l3 3" fill="none" stroke="#333" stroke-width=".8"/></svg>
  <div class="partners">
    <div class="partner"><span class="partner__dot"></span>Northwake<br>Expeditions</div>
    <div class="partner">Trailbound<br>North</div>
    <div class="partner">DMX Global</div>
    <div class="partner">Seaward Voyages</div>
  </div>
  <svg class="arrow arrow--next" viewBox="0 0 10 10"><path d="M1 5h8M6 2l3 3-3 3" fill="none" stroke="#333" stroke-width=".8"/></svg>

  <h2 class="section-title section-title--offers">Best Offers for Adventure</h2>
  <div class="offers offers--row1">
    <article>
      <div class="offer__photo" role="img" aria-label="Cruise ship in front of a blue glacier" style="background:linear-gradient(180deg,#8ec4e6,#cfe6f0 45%,#3fa3c9)"></div>
      <h3 class="offer__title">Our top ocean cruises vacation partners</h3>
      <p class="offer__text">Free First Class Air Upgrades from Vancouver, Toronto &amp; Montreal on select Alaska, Caribbean &amp; Canada/New England voyages | Offer Expires October 31, 2022</p>
    </article>
    <article>
      <div class="offer__photo" role="img" aria-label="Surf simulator on a ship deck above the ocean" style="background:linear-gradient(180deg,#a9cde0,#3b8fcf 50%,#1e6db3)"></div>
      <h3 class="offer__title">Discover the best of Alaska from one charming town to the next</h3>
      <p class="offer__text">Ovation Star May 11, 2023 Departure | 8 Night Alaska Glacier Cruise | Offer Expires October 2, 2022</p>
    </article>
    <article>
      <div class="offer__photo" role="img" aria-label="Hilltop stone fortress above green countryside" style="background:linear-gradient(180deg,#7fb6e3,#7d9a6a 50%,#5f7a4a)"></div>
      <h3 class="offer__title">Double stateroom upgrade</h3>
      <p class="offer__text">2023 Sailings | Change The Way You Sea | Inclusive Amenities | Offer expires December 9, 2022</p>
    </article>
  </div>
  <div class="offers" style="top:639px">
    <article>
      <div class="offer__photo" role="img" aria-label="Misty mountains and pine forest above a turquoise lake" style="background:linear-gradient(180deg,#c8d2d4,#7f8e88 40%,#2f5a3a 65%,#2f8f96)"></div>
      <h3 class="offer__title">Free first class air on select voyages</h3>
      <p class="offer__text">First Class In Every Way | 2023 Departures | Offer expires October 31, 2022</p>
    </article>
    <article>
      <div class="offer__photo" role="img" aria-label="Cruise ship docked by a tropical island water park" style="background:linear-gradient(180deg,#6fb6e8,#2a8fc4 50%,#c89a6a)"></div>
      <h3 class="offer__title">Save 30% off every guest</h3>
      <p class="offer__text">2023 Departure | 7-Night Eastern Caribbean Cruise | Offer expires October 2, 2022</p>
    </article>
    <article>
      <div class="offer__photo" role="img" aria-label="Bow of a cruise ship cutting through blue water" style="background:linear-gradient(180deg,#8fbfe6,#2c63a6 55%,#1d4f8c)"></div>
      <h3 class="offer__title">The sea romance sale</h3>
      <p class="offer__text">The Romance of the High Seas | The Sea Romance | Offer expires October 31, 2022</p>
    </article>
  </div>

  <footer class="footer">
    <div class="footer__col footer__col--left">
      <div class="footer__row"><svg viewBox="0 0 8 8"><circle cx="4" cy="4" r="3.5" fill="#f5a623"/><path d="M4 2v2h1.5" stroke="#0b4a66" stroke-width=".8" fill="none"/></svg>Hours 07:45 - 16:00 (AT)</div>
      <div class="footer__row"><svg viewBox="0 0 8 8"><path d="M4 .5a2.6 2.6 0 0 1 2.6 2.6C6.6 5 4 7.5 4 7.5S1.4 5 1.4 3.1A2.6 2.6 0 0 1 4 .5z" fill="#f5a623"/></svg>12 Harbour Lane, Douglas, NB, E3G 1A1, Canada</div>
    </div>
    <div class="footer__col footer__col--right">
      <div class="footer__row"><svg viewBox="0 0 8 8"><path d="M1.5 1l1.5-.5 1 2-1 .8a4 4 0 0 0 1.7 1.7l.8-1 2 1-.5 1.5C3.5 7 1 4.5 1.5 1z" fill="#f5a623"/></svg>555-014-2290</div>
      <div class="footer__row"><svg viewBox="0 0 8 8"><rect x=".5" y="1.5" width="7" height="5" fill="#f5a623"/><path d="M.5 1.5L4 4.3l3.5-2.8" stroke="#0b4a66" stroke-width=".6" fill="none"/></svg>hello@brightpathholidays.ca</div>
    </div>
    <div class="social"><span></span><span></span></div>
    <p class="copyright">© 2022 Bright Path Holidays &nbsp;|&nbsp; Privacy Policy &nbsp;|&nbsp; Terms of Use</p>
  </footer>
</section>

</body>
</html>
```